Create a memorable Stationary for Security Software Company

Velbrantix is the worldwide leader in securing the Internet. Making Internet communications and critical data secure, reliable and available everywhere has been and continues to be our ongoing vision. We are committed to staying focused on real customer needs and to developing new and innovative security solutions that redefine the security landscape.

Industry/Entity Type

Internet

Font styles to use
Serif
Sans Serif
Script

Colors
0792cd
33a6d7
85cae6

```html
<!DOCTYPE html>
<html lang="en">
<head>
<meta charset="utf-8">
<title>Velbrantix Business Card</title>
<link href="https://fonts.googleapis.com/css2?family=Open+Sans:wght@400;600&display=swap" rel="stylesheet">
<style>
  :root {
    --page-bg: #e6e8ea;
    --brand-deep: #0792cd;
    --brand-mid: #33a6d7;
    --brand-light: #85cae6;
    --card-shade: #2a7fbf;
    --name-ink: #1c5d8e;
    --text-light: #f2f8fc;
    --icon-ink: #1d5c8a;
  }
  * { margin: 0; padding: 0; box-sizing: border-box; }
  html, body {
    width: 1200px;
    height: 969px;
    overflow: hidden;
    background: var(--page-bg);
    font-family: "Open Sans", sans-serif;
  }
  .canvas {
    position: relative;
    width: 1200px;
    height: 969px;
  }
  .business-card {
    position: absolute;
    left: 100px;
    top: 200px;
    width: 1000px;
    height: 570px;
    border-radius: 34px;
    overflow: hidden;
    background: linear-gradient(135deg, var(--card-shade) 0%, var(--brand-deep) 40%, var(--brand-mid) 75%, var(--brand-light) 100%);
    box-shadow: 0 12px 34px rgba(20, 60, 90, 0.25);
  }
  .brand-panel {
    position: absolute;
    inset: 0;
  }
  .contact-block {
    position: absolute;
    left: 83px;
    top: 80px;
    color: var(--text-light);
  }
  .person-name {
    font-size: 34px;
    font-weight: 600;
    color: var(--name-ink);
    line-height: 1.15;
  }
  .person-title {
    font-size: 27px;
    font-weight: 400;
    line-height: 1.25;
  }
  .address {
    margin-top: 92px;
    font-size: 25px;
    line-height: 39px;
  }
  .contact-list {
    list-style: none;
    margin-top: 14px;
  }
  .contact-list li {
    display: flex;
    align-items: center;
    height: 41px;
    font-size: 25px;
  }
  .contact-icon {
    width: 22px;
    height: 22px;
    margin-right: 20px;
    fill: var(--icon-ink);
    flex-shrink: 0;
  }
  .brand-mark {
    position: absolute;
    left: 700px;
    top: 240px;
    display: flex;
    align-items: center;
    gap: 14px;
  }
  .brand-dot {
    width: 34px;
    height: 34px;
    border-radius: 50%;
    background: var(--name-ink);
  }
  .brand-name {
    font-size: 46px;
    font-weight: 600;
    color: var(--name-ink);
  }
</style>
</head>
<body>
<main class="canvas">
  <section class="business-card">
    <svg class="brand-panel" width="1000" height="570" viewBox="0 0 1000 570" aria-hidden="true">
      <path d="M560 0 C470 90 460 180 510 285 C560 390 540 480 470 570 L1000 570 L1000 0 Z" fill="#85cae6" fill-opacity="0.35"/>
    </svg>

    <div class="contact-block">
      <h1 class="person-name">Mara Ellison</h1>
      <p class="person-title">CEO/Founder</p>
      <p class="address">4120 Harbor Ridge Road<br>Tacoma, Washington 98402</p>
      <ul class="contact-list">
        <li>
          <svg class="contact-icon" viewBox="0 0 24 24"><path d="M6.6 10.8c1.4 2.8 3.8 5.1 6.6 6.6l2.2-2.2c.3-.3.7-.4 1-.2 1.1.4 2.3.6 3.6.6.6 0 1 .4 1 1V20c0 .6-.4 1-1 1C10.6 21 3 13.4 3 4c0-.6.4-1 1-1h3.5c.6 0 1 .4 1 1 0 1.3.2 2.5.6 3.6.1.3 0 .7-.2 1z"/></svg>
          555 218 4073
        </li>
        <li>
          <svg class="contact-icon" viewBox="0 0 24 24"><path d="M6 2h12v6H6zM3 9h18c1.1 0 2 .9 2 2v6h-4v5H5v-5H1v-6c0-1.1.9-2 2-2zm4 8v3h10v-3z"/></svg>
          555 730 6192
        </li>
        <li>
          <svg class="contact-icon" viewBox="0 0 24 24"><path d="M2 5h20v14H2zm2 2v.5l8 5 8-5V7l-8 5z"/></svg>
          mara@velbrantix.com
        </li>
        <li>
          <svg class="contact-icon" viewBox="0 0 24 24"><circle cx="12" cy="12" r="10"/><path d="M2 12h20M12 2c3 3 3 17 0 20M12 2c-3 3-3 17 0 20" stroke="#85cae6" stroke-width="1.4" fill="none"/></svg>
          www.velbrantix.com
        </li>
      </ul>
    </div>

    <div class="brand-mark">
      <span class="brand-dot"></span>
      <span class="brand-name">Velbrantix</span>
    </div>
  </section>
</main>
</body>
</html>
```